New business card/stationary for a consulting company

I am looking for a clean and very professional looking business card for my consulting company as well as corresponding stationary. I am uploading our logo. I like simple and powerful for the feel. No graphics but I am open on everything else. Below is my contact information but would like the final to be in a version I can add my employees information into and print. Thank you.

Daniel Whitcombe
dan@ferncliffadvisory.com
2870 North 9th Avenue, Summit Floor, Elm Ridge, Illinois 60531
www.ferncliffadvisory.com

Industry/Entity Type

Consulting

Contact Information for Business Card

Daniel Whitcombe
dan@ferncliffadvisory.com
www.ferncliffadvisory.com

Font styles to use
Serif
Sans Serif

Requirements
Must have
• Our logo and the business card details.
Nice to have
• our website www.ferncliffadvisory.com

```html
<!DOCTYPE html>
<html lang="en">
<head>
<meta charset="utf-8">
<title>Ferncliff Advisory — Business Card</title>
<link rel="stylesheet" href="https://fonts.googleapis.com/css2?family=Open+Sans:wght@400;700&display=swap">
<style>
  :root {
    --navy: #0b0a68;
    --paper: #fbfbfb;
    --ink-grey: #6a6a6a;
    --rule: #8a8a8a;
    --backdrop: #d9d9db;
  }
  html, body {
    margin: 0;
    padding: 0;
    width: 1200px;
    height: 904px;
    overflow: hidden;
    background: var(--backdrop);
    font-family: "Open Sans", sans-serif;
  }
  .stage {
    position: relative;
    width: 1200px;
    height: 904px;
  }
  .card {
    position: absolute;
    left: 240px;
    width: 720px;
    height: 411px;
    box-shadow: 0 6px 18px rgba(0,0,0,0.18);
  }
  .card-front {
    top: 26px;
    background: var(--navy);
    display: flex;
    align-items: center;
    justify-content: center;
  }
  .front-mark {
    display: flex;
    align-items: center;
    gap: 12px;
    color: #ffffff;
    font-size: 26px;
    font-weight: 400;
    letter-spacing: 2px;
  }
  .front-mark .mark-square {
    width: 18px;
    height: 18px;
    background: #ffffff;
  }
  .card-back {
    top: 467px;
    background: var(--paper);
  }
  .brand-name {
    position: absolute;
    left: 52px;
    top: 190px;
    width: 300px;
    text-align: center;
    color: var(--navy);
    font-size: 21px;
    font-weight: 400;
    letter-spacing: 1.5px;
    line-height: 1.35;
  }
  .divider {
    position: absolute;
    left: 392px;
    top: 120px;
    width: 1px;
    height: 175px;
    background: var(--rule);
  }
  .contact {
    position: absolute;
    left: 432px;
    top: 118px;
    color: var(--ink-grey);
    font-size: 14px;
    line-height: 1.45;
  }
  .contact-name {
    margin: 0 0 10px;
    color: var(--navy);
    font-size: 20px;
    font-weight: 700;
  }
  .contact-address {
    margin: 0 0 16px;
    padding-left: 14px;
  }
  .contact-line {
    display: flex;
    align-items: center;
    gap: 8px;
    padding-left: 14px;
    margin: 2px 0;
  }
  .contact-line svg {
    flex: none;
  }
</style>
</head>
<body>
<main class="stage">
  <section class="card card-front">
    <div class="front-mark">
      <span class="mark-square"></span>
      <span>FERNCLIFF ADVISORY</span>
    </div>
  </section>

  <section class="card card-back">
    <div class="brand-name">FERNCLIFF ADVISORY</div>
    <div class="divider"></div>
    <div class="contact">
      <p class="contact-name">Daniel Whitcombe</p>
      <p class="contact-address">2870 North 9th Avenue<br>Summit Floor, Elm Ridge<br>Illinois 60531</p>
      <div class="contact-line">
        <svg width="16" height="16" viewBox="0 0 16 16" aria-hidden="true">
          <circle cx="8" cy="8" r="8" fill="var(--navy)"/>
          <rect x="4" y="5" width="8" height="6" fill="none" stroke="#fff" stroke-width="1"/>
          <polyline points="4,5 8,8.5 12,5" fill="none" stroke="#fff" stroke-width="1"/>
        </svg>
        <span>dan@ferncliffadvisory.com</span>
      </div>
      <div class="contact-line">
        <svg width="16" height="16" viewBox="0 0 16 16" aria-hidden="true">
          <circle cx="8" cy="8" r="8" fill="var(--navy)"/>
          <circle cx="8" cy="8" r="4.5" fill="none" stroke="#fff" stroke-width="1"/>
          <ellipse cx="8" cy="8" rx="2" ry="4.5" fill="none" stroke="#fff" stroke-width="0.9"/>
          <line x1="3.5" y1="8" x2="12.5" y2="8" stroke="#fff" stroke-width="0.9"/>
        </svg>
        <span>www.ferncliffadvisory.com</span>
      </div>
    </div>
  </section>
</main>
</body>
</html>
```